Business Cards for new orthopaedic surgery practice

My husband and I are starting our own orthopaedic surgery practice. We are looking for a business card that is uniform, but one will have my name/title and the other will have his. You can just create one design with my name on it for now. But when I choose your design as the winning design I will ask that you add another copy with his name/title.

We are looking for classy, simple, elite all in one. We like dark blues/a little gold/yellow. Something that goes with our logo. We want our logo incorporated. Here is all the info you need:
Business name: RV Bone & Vitality Center
Location: 38517 North Willowmere Ave
Maple Hollow, FL 33418
Phone: 954-218-4063
Fax: 954-582-7341
Email: info@myrvbonecare.example

Names: Lydia Vance, M.D.
Board Certified Hand and Upper Extremity Surgeon

Ebo Dansu, M.D.
Board Certified Hip & Knee Replacement/General Orthopaedic Surgeon

Can decide what you want to put on the back. Maybe a slogan:
Rooted in Care. Focused on You

I am just going to upload our logo. The only thing is if we select you as the winning design, the location, and phone numbers may change. We will need your help to update that once fully solidified.

Industry/Entity Type

Medical

Contact Information for Business Card

Colors
0054AA
0677BA
7BADD7
CADEEF
E8F1F8
0094D4
00A9DD
6FCCEA
C7EBF8
E9F6FB

Requirements
Must have
• class, appeal,
Should not have
• We want to air on the side of masculine if we are looking at masculine vs. feminine feel. But we still want it classy, sophisticated, and something we will love

```html
<!DOCTYPE html>
<html lang="en">
<head>
<meta charset="utf-8">
<title>RV Bone &amp; Vitality Center – Business Card</title>
<link rel="stylesheet" href="https://fonts.googleapis.com/css2?family=Montserrat:wght@400;500;600&display=swap">
<style>
  :root {
    --navy: #1f2c57;
    --navy-deep: #18234a;
    --gold: #c8a35a;
    --white: #ffffff;
    --backdrop: #e9ebef;
  }
  * { box-sizing: border-box; margin: 0; padding: 0; }
  html, body { width: 1200px; height: 1200px; overflow: hidden; }
  body {
    background: var(--backdrop);
    font-family: "Montserrat", Arial, sans-serif;
    position: relative;
  }
  .card {
    position: absolute;
    left: 150px;
    width: 900px;
    height: 514px;
    border-radius: 36px;
    overflow: hidden;
    background: var(--navy);
    box-shadow: 0 0 0 3px var(--gold), 0 14px 30px rgba(0,0,0,.18);
  }
  .card-front { top: 60px; }
  .card-back  { top: 626px; background: linear-gradient(160deg, var(--navy) 0%, var(--navy-deep) 100%); }
  .front-shape { position: absolute; inset: 0; width: 100%; height: 100%; }

  .contact-block {
    position: absolute;
    left: 64px;
    top: 150px;
    color: var(--white);
  }
  .doctor-name {
    color: var(--gold);
    font-weight: 600;
    font-size: 33px;
    letter-spacing: .5px;
    text-transform: uppercase;
  }
  .doctor-title {
    font-size: 21px;
    font-weight: 500;
    line-height: 1.15;
    margin-top: 6px;
  }
  .contact-list { list-style: none; margin-top: 30px; }
  .contact-item {
    display: flex;
    align-items: flex-start;
    gap: 16px;
    font-size: 20px;
    font-weight: 500;
    line-height: 1.2;
    margin-bottom: 9px;
  }
  .contact-icon { width: 24px; height: 24px; flex: none; margin-top: 1px; }

  .brand-lockup {
    position: absolute;
    text-align: center;
    display: flex;
    flex-direction: column;
    align-items: center;
    gap: 16px;
  }
  .brand-lockup-front { left: 560px; top: 150px; width: 300px; color: var(--navy); }
  .brand-lockup-back { left: 0; right: 0; top: 170px; color: var(--white); }
  .brand-dot { width: 26px; height: 26px; border-radius: 50%; background: var(--gold); }
  .brand-name {
    font-weight: 600;
    font-size: 30px;
    line-height: 1.25;
    letter-spacing: 1px;
  }
  .brand-lockup-back .brand-name { font-size: 40px; }
</style>
</head>
<body>

<section class="card card-front" aria-label="Business card front">
  <svg class="front-shape" viewBox="0 0 900 514" preserveAspectRatio="none" aria-hidden="true">
    <path d="M436,0 C466,300 680,500 900,514 L900,0 Z" fill="var(--white)"/>
    <path d="M444,0 C474,296 688,494 900,508 L900,0 Z" fill="var(--gold)"/>
    <path d="M462,0 C492,286 700,482 900,496 L900,0 Z" fill="var(--white)"/>
  </svg>

  <div class="contact-block">
    <h1 class="doctor-name">Lydia Vance, M.D.</h1>
    <p class="doctor-title">Board Certified Hand and<br>Upper Extremity Surgeon</p>
    <ul class="contact-list">
      <li class="contact-item">
        <svg class="contact-icon" viewBox="0 0 24 24"><path fill="var(--gold)" d="M6.6 10.8a15 15 0 0 0 6.6 6.6l2.2-2.2c.3-.3.7-.4 1-.2 1.1.4 2.3.6 3.6.6.6 0 1 .4 1 1V20c0 .6-.4 1-1 1A17 17 0 0 1 3 4c0-.6.4-1 1-1h3.5c.6 0 1 .4 1 1 0 1.3.2 2.5.6 3.6.1.3 0 .7-.2 1z"/></svg>
        <span>954-218-4063</span>
      </li>
      <li class="contact-item">
        <svg class="contact-icon" viewBox="0 0 24 24"><g fill="none" stroke="var(--gold)" stroke-width="2"><rect x="3" y="9" width="18" height="11" rx="1.5"/><path d="M7 9V3h10v6"/><path d="M7 13h3M7 16h3M13 13h4M13 16h4"/></g></svg>
        <span>954-582-7341</span>
      </li>
      <li class="contact-item">
        <svg class="contact-icon" viewBox="0 0 24 24"><g fill="none" stroke="var(--gold)" stroke-width="2"><rect x="2" y="5" width="20" height="14" rx="1"/><path d="M2 6l10 7 10-7"/></g></svg>
        <span>info@myrvbonecare.example</span>
      </li>
      <li class="contact-item">
        <svg class="contact-icon" viewBox="0 0 24 24"><path fill="var(--gold)" d="M12 2a7 7 0 0 0-7 7c0 5 7 13 7 13s7-8 7-13a7 7 0 0 0-7-7zm0 9.5A2.5 2.5 0 1 1 12 6.5a2.5 2.5 0 0 1 0 5z"/></svg>
        <span>38517 North Willowmere Ave<br>Maple Hollow, FL 33418</span>
      </li>
    </ul>
  </div>

  <div class="brand-lockup brand-lockup-front">
    <span class="brand-dot" aria-hidden="true"></span>
    <p class="brand-name">RV Bone &amp;<br>Vitality Center</p>
  </div>
</section>

<section class="card card-back" aria-label="Business card back">
  <div class="brand-lockup brand-lockup-back">
    <span class="brand-dot" aria-hidden="true"></span>
    <p class="brand-name">RV Bone &amp;<br>Vitality Center</p>
  </div>
</section>

</body>
</html>
```